BOLD & MINIMALIST DESIGN NEEDED

We want a very bold but minimalistic business card design that is impactful and utilizes both sides of the business card. Our current logo is included for your use.

We want bold fonts and good use of negative space. We don't want the logo to overpower the design.

Target Market(s)

Professionals who are building new commercial buildings.

Industry/Entity Type

Construction

Contact Information for Business Card

Name, Title, email, office phone, cell phone, website

Font styles to use
Serif
Sans Serif

Requirements
Must have
• Bold design!

```html
<!DOCTYPE html>
<html lang="en">
<head>
<meta charset="utf-8">
<title>Northcrest Business Card</title>
<link rel="stylesheet" href="https://fonts.googleapis.com/css2?family=Montserrat:wght@600;700&family=Roboto:wght@400&display=swap">
<style>
  :root {
    --bg: #e4e4e4;
    --paper: #ffffff;
    --ink: #111111;
    --text-grey: #555555;
    --rule: #d6d6d6;
    --green: #7cc33a;
    --green-light: #a6d96a;
    --charcoal: #2f2f2f;
  }
  * { margin: 0; padding: 0; box-sizing: border-box; }
  html, body { width: 1200px; height: 1200px; overflow: hidden; background: var(--bg); }
  .canvas { position: relative; width: 1200px; height: 1200px; }

  .card {
    position: absolute;
    left: 255px;
    width: 690px;
    height: 394px;
    overflow: hidden;
  }
  .card-front { top: 150px; background: var(--paper); }
  .card-back { top: 650px; background: var(--charcoal); }

  .brand {
    position: absolute;
    display: flex;
    align-items: center;
    gap: 12px;
    font-family: "Montserrat", sans-serif;
    font-weight: 700;
    letter-spacing: 1px;
  }
  .brand-front { right: 48px; top: 150px; color: var(--ink); font-size: 34px; }
  .brand-mark { width: 22px; height: 22px; background: var(--green); }

  .holder { position: absolute; left: 48px; top: 238px; }
  .holder-name {
    font-family: "Montserrat", sans-serif;
    font-weight: 700;
    font-size: 28px;
    color: var(--ink);
    letter-spacing: 0.5px;
    line-height: 1;
  }
  .holder-title {
    font-family: "Roboto", sans-serif;
    font-size: 16px;
    color: var(--green);
    margin-top: 4px;
  }

  .divider {
    position: absolute;
    left: 48px; right: 48px; top: 302px;
    height: 1px; background: var(--rule);
  }

  .contact {
    position: absolute;
    top: 312px;
    font-family: "Roboto", sans-serif;
    font-size: 16px;
    color: var(--text-grey);
    line-height: 20px;
  }
  .contact-phones { left: 48px; }
  .contact-web { right: 48px; text-align: right; }
  .contact-row { display: flex; align-items: center; gap: 8px; }
  .contact-web .contact-row { justify-content: flex-end; }
  .icon { width: 14px; height: 14px; flex: none; }

  .band { position: absolute; top: 378px; height: 16px; }
  .band-dark { left: 0; width: 418px; background: var(--ink); }
  .band-green {
    left: 422px; right: 0;
    background: linear-gradient(90deg, var(--green), var(--green-light) 55%, var(--green));
  }

  .brand-back {
    left: 0; right: 0; top: 150px;
    justify-content: center;
    color: #ffffff;
    font-size: 46px;
    letter-spacing: 3px;
  }
  .brand-back .brand-mark { width: 30px; height: 30px; }
  .back-url {
    position: absolute;
    left: 0; right: 0; top: 330px;
    text-align: center;
    font-family: "Montserrat", sans-serif;
    font-weight: 600;
    font-size: 16px;
    letter-spacing: 3px;
    color: #ffffff;
  }
  .back-url .accent { color: var(--green); }
</style>
</head>
<body>
<main class="canvas">

  <section class="card card-front">
    <div class="brand brand-front">
      <span class="brand-mark"></span>
      <span class="brand-name">NORTHCREST</span>
    </div>

    <div class="holder">
      <h1 class="holder-name">DANIEL CARTER</h1>
      <p class="holder-title">President</p>
    </div>

    <div class="divider"></div>

    <div class="contact contact-phones">
      <div class="contact-row">
        <svg class="icon" viewBox="0 0 16 16" aria-hidden="true"><path fill="#111" d="M3.6 1.2l2.3 2.4-1.3 2a9 9 0 0 0 5.8 5.8l2-1.3 2.4 2.3-1.5 2.3C7.5 16.4-.4 8.5 1.3 2.7z"/></svg>
        <span>555-201-4830</span>
      </div>
      <div class="contact-row">
        <svg class="icon" viewBox="0 0 16 16" aria-hidden="true"><rect x="3.5" y="0.8" width="9" height="14.4" rx="1.4" fill="none" stroke="#111" stroke-width="1.6"/><rect x="7" y="12" width="2" height="1.4" fill="#111"/></svg>
        <span>555-309-7162</span>
      </div>
    </div>

    <div class="contact contact-web">
      <div class="contact-row">
        <span>info@northcrest.com</span>
        <svg class="icon" viewBox="0 0 16 16" aria-hidden="true"><rect x="1" y="3" width="14" height="10" fill="#111"/><path d="M1.5 3.5L8 9l6.5-5.5" fill="none" stroke="#fff" stroke-width="1.2"/></svg>
      </div>
      <div class="contact-row">
        <span>www.northcrest.com</span>
        <svg class="icon" viewBox="0 0 16 16" aria-hidden="true"><circle cx="8" cy="8" r="7" fill="#111"/><path d="M8 1v14M1 8h14M8 1c-3 3-3 11 0 14M8 1c3 3 3 11 0 14" fill="none" stroke="#fff" stroke-width="0.9"/></svg>
      </div>
    </div>

    <div class="band band-dark"></div>
    <div class="band band-green"></div>
  </section>

  <section class="card card-back">
    <div class="brand brand-back">
      <span class="brand-mark"></span>
      <span class="brand-name">NORTHCREST</span>
    </div>
    <p class="back-url">www.<span class="accent">northcrest</span>.com</p>
  </section>

</main>
</body>
</html>
```